Social Media App Needs PPT Template

We need a PowerPoint template for a new social media company based in the DC area called "Bold Ledger." We provide an interactive digital platform for executives to share actionable advice. We would like to see designs that use our orange logo color as an accent, but are mainly grey, white, and black. The final design should communicate clean, chic, modern, and professional.

Target Market(s)

Executives

Industry/Entity Type

Information Technology

Font styles to use
Sans Serif

Colors
f78f20
fbe7d2
ffffff
000000
e8e8e8
757575

Requirements
Must have
• My project must have title page and many options for the body of the ppt (graphs, tables, etc). It also needs to be easy to modify. I must have someone who is experienced in creating powerpoint templates.
Nice to have
• It would be nice to have a very modern and clean design that includes the logo on every page, but still leaves a lot of room for the content of the slide
Should not have
• My design project should not look to busy.

```html
<!DOCTYPE html>
<html lang="en">
<head>
<meta charset="utf-8">
<title>About Our Company – Bold Ledger</title>
<link href="https://fonts.googleapis.com/css2?family=Lato:wght@300;400;700&display=swap" rel="stylesheet">
<style>
  :root {
    --orange: #f78f20;
    --orange-deep: #e8821a;
    --black: #000000;
    --ink: #0f1420;
    --text: #3a3a3a;
    --muted: #757575;
    --backdrop: #939393;
    --sheet: #f4f4f4;
    --white: #ffffff;
  }
  * { box-sizing: border-box; margin: 0; padding: 0; }
  html, body { width: 1200px; height: 960px; overflow: hidden; }
  body {
    background: var(--backdrop);
    font-family: "Lato", sans-serif;
    position: relative;
  }
  .page-label {
    position: absolute; top: 44px; left: 0; width: 1200px;
    text-align: center; color: var(--white);
    font-weight: 300; font-size: 26px; letter-spacing: 0.5px;
  }
  .slide {
    position: absolute; left: 68px; top: 106px;
    width: 1062px; height: 796px;
    background: radial-gradient(ellipse at 50% 35%, #fbfbfb 0%, var(--sheet) 60%, #ececec 100%);
    overflow: hidden;
  }
  .slide-header, .slide-footer { position: absolute; left: 0; }
  .slide-header { top: 0; }
  .slide-footer { top: 755px; }
  .slide-title {
    position: absolute; left: 32px; top: 68px;
    color: var(--white); font-weight: 300; font-size: 42px; line-height: 1;
  }
  .brand {
    position: absolute; left: 858px; top: 76px;
    display: flex; align-items: center; gap: 10px;
    color: var(--white); font-weight: 700; font-size: 24px; line-height: 1;
  }
  .brand-dot { width: 30px; height: 30px; border-radius: 50%; background: var(--orange); }
  .team { position: absolute; top: 226px; left: 36px; display: flex; gap: 57px; }
  .member { width: 289px; }
  .member-photo {
    width: 289px; height: 174px;
    border: 2px solid var(--orange);
  }
  .photo-office { background: linear-gradient(135deg, #e9e6e1 0%, #c9b9a8 50%, #aebfd4 100%); }
  .photo-window { background: linear-gradient(135deg, #bcd6e6 0%, #8a8f99 55%, #2a2f3a 100%); }
  .photo-park { background: linear-gradient(135deg, #8a9a5a 0%, #a89a7a 50%, #b9c3cf 100%); }
  .member-name {
    margin-top: 20px; font-weight: 700; font-size: 22px; color: var(--ink); line-height: 1.2;
  }
  .member-role {
    margin-top: 2px; font-weight: 300; font-size: 16px; color: var(--muted);
  }
  .member-rule { margin-top: 10px; height: 2px; background: var(--ink); }
  .member-bio {
    margin-top: 20px; font-size: 15.6px; line-height: 19.6px;
    color: var(--text); text-align: justify;
  }
  .member-rule-bottom { margin-top: 30px; height: 2px; background: var(--ink); }
  .footer-text {
    position: absolute; left: 29px; top: 763px;
    color: var(--white); font-size: 14px; font-weight: 400;
  }
  .footer-text .sep { margin: 0 6px; }
</style>
</head>
<body>
  <div class="page-label">Page 10</div>

  <section class="slide">
    <svg class="slide-header" width="1062" height="150" viewBox="0 0 1062 150">
      <polygon points="832,36 1062,36 1062,46 822,46" fill="var(--orange)"/>
      <polygon points="0,50 804,50 720,134 0,134" fill="var(--orange-deep)"/>
      <polygon points="560,50 804,50 720,134 640,134" fill="var(--orange)" opacity="0.55"/>
      <polygon points="813,50 1062,50 1062,134 729,134" fill="var(--black)"/>
      <polygon points="0,138 716,138 706,148 0,148" fill="var(--black)"/>
    </svg>
    <h1 class="slide-title">About Our Company</h1>
    <div class="brand"><span class="brand-dot"></span>Bold Ledger</div>

    <div class="team">
      <article class="member">
        <div class="member-photo photo-office" role="img" aria-label="Portrait of a smiling executive in an office"></div>
        <h2 class="member-name">Mr D. Smilth</h2>
        <p class="member-role">(President)</p>
        <div class="member-rule"></div>
        <p class="member-bio">Lorem ipsum dolor sit amet, consectetuer adipiscing elit, sed diam nonummy nibh euismod tincidunt ut laoreet dolore magna aliquam erat volutpat. Ut wisi enim ad minim veniam, quis nostrud exerci tation ullamcorper suscipit lobortis nisl ut aliquip ex ea commodo consequat.</p>
        <div class="member-rule-bottom"></div>
      </article>
      <article class="member">
        <div class="member-photo photo-window" role="img" aria-label="Portrait of an executive in a dark suit"></div>
        <h2 class="member-name">Mr D. Smilth</h2>
        <p class="member-role">(President)</p>
        <div class="member-rule"></div>
        <p class="member-bio">Lorem ipsum dolor sit amet, consectetuer adipiscing elit, sed diam nonummy nibh euismod tincidunt ut laoreet dolore magna aliquam erat volutpat. Ut wisi enim ad minim veniam, quis nostrud exerci tation ullamcorper suscipit lobortis nisl ut aliquip ex ea commodo consequat.</p>
        <div class="member-rule-bottom"></div>
      </article>
      <article class="member">
        <div class="member-photo photo-park" role="img" aria-label="Portrait of a smiling executive outdoors"></div>
        <h2 class="member-name">Mr D. Smilth</h2>
        <p class="member-role">(President)</p>
        <div class="member-rule"></div>
        <p class="member-bio">Lorem ipsum dolor sit amet, consectetuer adipiscing elit, sed diam nonummy nibh euismod tincidunt ut laoreet dolore magna aliquam erat volutpat. Ut wisi enim ad minim veniam, quis nostrud exerci tation ullamcorper suscipit lobortis nisl ut aliquip ex ea commodo consequat.</p>
        <div class="member-rule-bottom"></div>
      </article>
    </div>

    <svg class="slide-footer" width="1062" height="31" viewBox="0 0 1062 31">
      <polygon points="318,0 1062,0 1062,31 288,31" fill="var(--orange-deep)"/>
      <polygon points="0,0 303,0 273,31 0,31" fill="var(--black)"/>
    </svg>
    <p class="footer-text">www.boldledger.com<span class="sep">|</span>Page 8</p>
  </section>
</body>
</html>
```